Start up International Security Business Needs a Web Design

Based in Edinburgh UK, Morvane Global Services (www.morvanegs.example) provides security services of various types in challenging or high threat environments internationally for government and private sector organizations. We provide risk assessments, security audits and training, medical support, close protection for individuals, groups and events, crisis management, and evacuation coordination; we enable businesses to operate in challenging locations. Our experts are highly trained and qualified with exceptional experience worldwide.
The name Morvane was selected in competition and derives from Greek Mythology where it was a giant man of bronze gifted by Zeus to protect Europa from invaders and pirates, circling the island of Crete three times daily (essentially establishing a protective perimeter). The centre of the current logo (inside the "O") is a stylized symbol of Zeus; we use it as a customized "bullet" on documents and acts as an abbreviated logo.
We purposefully omitted any reference to security in the name/logo and the web-page should be discreet in the same manner - we provide services of this nature but do not draw attention to ourselves. Generic images for visuals should be used as opposed to any existing stock photography we possess as a company. Imagery that relay protection, an international reach, innovation, modern vistas, varied countrysides (desert, jungle, urban settings, an old fortress?) would be seen positively.
The current colour of blue and white in the principal logo has received positive response for the clean lines, and the grey-ish scale writing similarly works. The "O" with the symbol inside has been used as customized "bullets" inside of documents, and we envisioned several other potential uses for web pages, etc.
However the integration of bronze as a third colour given the origin of Morvane could be a consideration as well.
The final design should communicate clarity, an international reach in difficult areas with our broad experience and strength without being aggressive. There must be a section where the countries we have experience operating in is displayed graphically (i.e. a global map where the countries are coloured in). Countries are USA, Canada, UK, France, Bosnia, UAE, Qatar, Libya, Tunisia, Afghanistan, Iraq, Turkey, Sudan, Egypt, Central African Republic, Somalia, Rwanda, Somaliland. Additional sections should include "Our Clients", "Our Services", "Our Expertise", "Join Our Team" which should have a personal details form and ability to upload a CV, "Our Contact Details" which should also allow for submission of a web enquiry
Reason: Extension granted at the request of several designers in order to conceptualize solutions whilst initial selection process begins. Feedback on each design submitted will be provided. Very many thanks to all who took the time to share their vision for our company's website.
Morvane GS
Target Market(s)
Private Sector energy, logistics, and infrastructure companies along with government organizations
Industry/Entity Type
Security
Logo Text
Morvane
Number of Pages Required
3 page
Requirements
Must have
- There must be a section where the countries we have experience operating in is displayed graphically (i.e. a global map where the countries are coloured in). Countries are USA, Canada, UK, France, Bosnia, UAE, Qatar, Libya, Tunisia, Afghanistan, Iraq, Turkey, Sudan, Egypt, Central African Republic, Somalia, Rwanda, Somaliland. Additional sections should include "Our Clients", "Our Services", "Our Expertise", "Join Our Team" which should have a personal details form and ability to upload a CV, "Our Contact Details" which should also allow for submission of a web enquiry
Should not have
- Aggressive pictures of guards, weapons, etc

```html
<!DOCTYPE html>
<html lang="en">
<head>
<meta charset="utf-8">
<title>Morvane Global Services</title>
<link rel="stylesheet" href="https://fonts.googleapis.com/css2?family=Open+Sans:wght@300;400;600;700&family=Lato:wght@400;700&display=swap">
<style>
:root{
  --brand-blue:#0f4f9c;
  --ink:#2b2b2b;
  --muted:#8f98a3;
  --soft-text:#b0b7c0;
  --pin-orange:#efa047;
  --pin-blue:#35a3d3;
  --footer-bg:#232323;
  --footer-text:#9a9a9a;
  --map-grey:#cfcfcf;
  --tile-blue:#d6e3f0;
  --tile-mint:#c4ecdf;
  --tile-pink:#f6d1d6;
  --tile-grey:#d9dfe3;
  --tile-navy:#1f2535;
  --tile-peach:#fde3cc;
  --tile-lilac:#ecd9e2;
}
*{margin:0;padding:0;box-sizing:border-box}
html,body{width:1200px;height:2830px;overflow:hidden}
body{position:relative;background:#fff;font-family:"Open Sans",Arial,sans-serif;color:var(--ink)}
.abs{position:absolute}

/* Hero */
.hero{left:0;top:0;width:1200px;height:679px;background:radial-gradient(circle at 900px 470px,#7fcfee 0,#3d7fa0 60px,#8d979d 170px,#b9c0c4 360px,#8e969b 800px)}
.hero-menu{right:22px;top:18px;width:32px}
.hero-menu span{display:block;height:3px;background:#fff;margin:5px 0}
.hero-arrow{top:322px}
.hero-box{left:192px;top:189px;width:818px;height:290px;background:rgba(235,238,240,.82);text-align:center}
.hero-name{margin-top:34px;font-size:52px;font-weight:700;color:var(--brand-blue);letter-spacing:1px;line-height:60px}
.hero-tagline{width:720px;margin:26px auto 0;font-size:18px;font-weight:600;line-height:28px;color:#1d1d1d}
.btn{display:inline-block;background:var(--brand-blue);color:#fff;font-size:13px;font-weight:600;text-transform:uppercase}
.hero-btn{margin-top:26px;padding:9px 18px}

/* Welcome */
.section-title{width:1200px;text-align:center;font-size:27px;font-weight:400;letter-spacing:.5px;color:#222}
.welcome-title{top:707px}
.welcome-copy{left:113px;top:760px;width:974px;text-align:center;font-size:12px;line-height:17px;color:#555}
.service{width:362px}
.service-left{left:108px;text-align:right}
.service-right{left:734px;text-align:left}
.service h3{font-family:"Lato",Arial,sans-serif;font-size:11.5px;font-weight:700;letter-spacing:1px;text-transform:uppercase;color:#222;margin-bottom:16px}
.service p{font-family:"Lato",Arial,sans-serif;font-size:11.5px;line-height:20px;color:var(--soft-text)}
.tile{width:102px;height:102px;display:flex;align-items:center;justify-content:center}
.tile-left{left:487px}
.tile-right{left:615px}

/* Contact band */
.cta-band{left:0;top:1464px;width:1200px;height:270px;background:radial-gradient(ellipse at 600px 520px,#28506c 0,#0d1c2c 260px,#05080f 520px)}
.cta-text{left:189px;top:1585px;font-size:19px;color:#fff;letter-spacing:.3px}
.cta-btn{left:857px;top:1578px;width:154px;height:41px;line-height:41px;text-align:center;font-size:14px}

/* Countries */
.countries-title{top:1808px}
.world-map{left:100px;top:1915px;width:1032px;height:519px;background:var(--map-grey);border-radius:40px;opacity:.75}
.pin{width:26px;height:34px}
.country-list{font-size:10px;line-height:25.5px;color:#333;text-transform:uppercase;list-style:none}
.country-list .active{color:var(--pin-blue);text-decoration:underline}

/* Footer */
.site-footer{left:0;top:2574px;width:1200px;height:256px;background:var(--footer-bg)}
.footer-col{top:2612px;width:349px;text-align:center;font-size:11.5px;line-height:19px;color:var(--footer-text)}
.footer-divider{top:2620px;width:1px;height:70px;background:#3a3a3a}
.social{top:2736px;width:26px;height:26px;border-radius:50%;background:#4a4a4a}
.social.is-active{background:var(--pin-blue)}
.copyright{top:2786px;width:1200px;text-align:center;font-size:10px;letter-spacing:1px;color:#6d6d6d}
</style>
</head>
<body>

<!-- Hero -->
<div class="abs hero" role="img" aria-label="Close-up photograph of a human eye with a glowing digital scanning interface"></div>
<div class="abs hero-menu" aria-label="Menu"><span></span><span></span><span></span></div>
<svg class="abs hero-arrow" style="left:28px" width="26" height="36" viewBox="0 0 26 36"><path d="M20 4 L6 18 L20 32" fill="none" stroke="#fff" stroke-width="4"/></svg>
<svg class="abs hero-arrow" style="left:1148px" width="26" height="36" viewBox="0 0 26 36"><path d="M6 4 L20 18 L6 32" fill="none" stroke="#fff" stroke-width="4"/></svg>
<div class="abs hero-box">
  <div class="hero-name">Morvane</div>
  <p class="hero-tagline">We provide security services of various types in challenging or high threat environments internationally for government and private sector organizations.</p>
  <span class="btn hero-btn">Read More</span>
</div>

<!-- Welcome -->
<h2 class="abs section-title welcome-title">WELCOME</h2>
<p class="abs welcome-copy">Donec ut mauris sit amet nunc feugiat pellentesque. Nulla ultrices nulla vitae turpis ultricies mollis. Nullam faucibus a augue nec placerat. Nullam a velit vitae erat posuere porta. Aliquam convallis blandit lacinia. Vivamus eu est massa. Morbi dolor tellus, auctor vel sapien id, posuere viverra purus. Nam ac nunc lectus. Cras mattis sollicitudin velit, et semper ex euismod sed. Cras eget vehicula dolor, id cursus purus. Ut sodales magna est, sed blandit tellus elementum a. Nullam sagittis quam nulla, sed lobortis nisi mollis eget. Proin efficitur sapien ante, ut venenatis urna varius eu. Donec non enim sit amet metus tempus pellentesque nec vitae odio. Nulla eu egestas sapien, sit amet auctor ex. Vivamus tempor vitae sem ac posuere.</p>

<!-- Service row 1 -->
<div class="abs service service-left" style="top:889px"><h3>Risk Assessments</h3><p>Phasellus ut condimentum diam, eget tempus lorem. Morbi bibendum est quis arcu posuere condimentum. Nullam justo eros, pellentesque a metus non, mattis volutpat libero. Praesent ornare felis ante.</p></div>
<div class="abs tile tile-left" style="top:893px;background:var(--tile-blue)"><svg width="40" height="36" viewBox="0 0 40 36"><path d="M20 3 L37 33 H3 Z" fill="none" stroke="#fff" stroke-width="3" stroke-linejoin="round"/><rect x="18.5" y="13" width="3" height="11" fill="#fff"/><rect x="18.5" y="26.5" width="3" height="3" fill="#fff"/></svg></div>
<div class="abs tile tile-right" style="top:893px;background:var(--tile-mint)"><svg width="36" height="42" viewBox="0 0 36 42"><path d="M18 2 L33 8 V20 C33 30 26 37 18 40 C10 37 3 30 3 20 V8 Z" fill="#fff"/><circle cx="18" cy="17" r="5" fill="var(--tile-mint)"/><path d="M9 30 C11 24 25 24 27 30" fill="var(--tile-mint)"/></svg></div>
<div class="abs service service-right" style="top:889px"><h3>Security Audits and Training</h3><p>Phasellus ut condimentum diam, eget tempus lorem. Morbi bibendum est quis arcu posuere condimentum. Nullam justo eros, pellentesque a metus non, mattis volutpat libero. Praesent ornare felis ante.</p></div>

<!-- Service row 2 -->
<div class="abs service service-left" style="top:1017px"><h3>And Evacuation Coordination</h3><p>Phasellus ut condimentum diam, eget tempus lorem. Morbi bibendum est quis arcu posuere condimentum. Nullam justo eros, pellentesque a metus non, mattis volutpat libero. Praesent ornare felis ante.</p></div>
<div class="abs tile tile-left" style="top:1021px;background:var(--tile-pink)"><svg width="34" height="38" viewBox="0 0 34 38"><path d="M6 4 H28 V32 H9 A3 3 0 0 1 6 29 Z" fill="#fff"/><path d="M6 29 A3 3 0 0 0 9 35 H30 V32" fill="none" stroke="#fff" stroke-width="2.5"/><path d="M11 11 H23 M11 16 H23" stroke="var(--tile-pink)" stroke-width="2"/></svg></div>
<div class="abs tile tile-right" style="top:1021px;background:var(--tile-grey)"><svg width="38" height="40" viewBox="0 0 38 40"><path d="M7 3 V14 A8 8 0 0 0 23 14 V3" fill="none" stroke="#fff" stroke-width="3"/><path d="M15 22 V28 A7 7 0 0 0 29 28 V22" fill="none" stroke="#fff" stroke-width="3"/><circle cx="29" cy="18" r="4" fill="none" stroke="#fff" stroke-width="3"/></svg></div>
<div class="abs service service-right" style="top:1017px"><h3>Medical Support</h3><p>Phasellus ut condimentum diam, eget tempus lorem. Morbi bibendum est quis arcu posuere condimentum. Nullam justo eros, pellentesque a metus non, mattis volutpat libero. Praesent ornare felis ante.</p></div>

<!-- Service row 3 -->
<div class="abs service service-left" style="top:1145px"><h3>Crisis Management</h3><p>Phasellus ut condimentum diam, eget tempus lorem. Morbi bibendum est quis arcu posuere condimentum. Nullam justo eros, pellentesque a metus non, mattis volutpat libero. Praesent ornare felis ante.</p></div>
<div class="abs tile tile-left" style="top:1149px;background:var(--tile-navy);outline:3px solid #fff;outline-offset:-8px;box-shadow:0 0 0 1px var(--tile-navy)"><svg width="40" height="34" viewBox="0 0 40 34"><path d="M3 30 V6 L14 20 L22 10 L33 22" fill="none" stroke="#fff" stroke-width="3"/><rect x="20" y="22" width="3" height="9" fill="#fff"/><rect x="26" y="18" width="3" height="13" fill="#fff"/><rect x="32" y="24" width="3" height="7" fill="#fff"/></svg></div>
<div class="abs tile tile-right" style="top:1149px;background:var(--tile-peach)"><svg width="34" height="36" viewBox="0 0 34 36"><circle cx="17" cy="10" r="8" fill="#fff"/><path d="M2 34 C3 22 31 22 32 34 Z" fill="#fff"/></svg></div>
<div class="abs service service-right" style="top:1145px"><h3>Close Protection for Individuals,</h3><p>Phasellus ut condimentum diam, eget tempus lorem. Morbi bibendum est quis arcu posuere condimentum. Nullam justo eros, pellentesque a metus non, mattis volutpat libero. Praesent ornare felis ante.</p></div>

<!-- Service row 4 -->
<div class="abs service service-left" style="top:1274px"><h3>Groups and Events</h3><p>Phasellus ut condimentum diam, eget tempus lorem. Morbi bibendum est quis arcu posuere condimentum. Nullam justo eros, pellentesque a metus non, mattis volutpat libero. Praesent ornare felis ante.</p></div>
<div class="abs tile tile-left" style="top:1278px;background:var(--tile-lilac)"><svg width="44" height="34" viewBox="0 0 44 34"><circle cx="22" cy="9" r="6" fill="#fff"/><circle cx="9" cy="12" r="4.5" fill="#fff"/><circle cx="35" cy="12" r="4.5" fill="#fff"/><path d="M12 31 C12 18 32 18 32 31 Z" fill="#fff"/><path d="M1 30 C1 20 15 20 14 26 L12 30 Z M43 30 C43 20 29 20 30 26 L32 30 Z" fill="#fff"/></svg></div>

<!-- Contact band -->
<div class="abs cta-band" role="img" aria-label="Night view of the earth from space with glowing network lines"></div>
<p class="abs cta-text">LOREM IPSUM DOLOR SIT AMET, CONSECTETUR ADIPISCING ELIT.</p>
<span class="abs btn cta-btn">Contact Now</span>

<!-- Countries -->
<h2 class="abs section-title countries-title">COUNTRIES WE HAVE EXPERIENCE</h2>
<div class="abs world-map" role="img" aria-label="Grey world map showing the countries of operation"></div>
<svg class="abs" style="left:0;top:0" width="1200" height="2830" viewBox="0 0 1200 2830" aria-hidden="true">
  <defs>
    <path id="pin-shape" d="M0 0 C-4 -8 -12 -12 -12 -21 A12 12 0 0 1 12 -21 C12 -12 4 -8 0 0 Z"/>
  </defs>
  <g font-family="Open Sans, Arial, sans-serif" font-size="10" font-weight="600" fill="#fff" text-anchor="middle">
    <g fill="var(--pin-orange)">
      <use href="#pin-shape" x="277" y="2074"/><use href="#pin-shape" x="540" y="2022"/><use href="#pin-shape" x="583" y="2071"/>
      <use href="#pin-shape" x="630" y="2056"/><use href="#pin-shape" x="615" y="2090"/><use href="#pin-shape" x="634" y="2120"/>
      <use href="#pin-shape" x="679" y="2124"/><use href="#pin-shape" x="708" y="2142"/><use href="#pin-shape" x="772" y="2146"/>
      <use href="#pin-shape" x="668" y="2171"/><use href="#pin-shape" x="711" y="2182"/><use href="#pin-shape" x="749" y="2180"/>
      <use href="#pin-shape" x="613" y="2197"/><use href="#pin-shape" x="666" y="2222"/><use href="#pin-shape" x="721" y="2216"/>
      <use href="#pin-shape" x="710" y="2233"/><use href="#pin-shape" x="653" y="2267"/>
    </g>
    <use href="#pin-shape" x="298" y="2131" fill="var(--pin-blue)"/>
    <text x="298" y="2114">1</text><text x="277" y="2057">2</text><text x="583" y="2054">3</text><text x="540" y="2005">4</text>
    <text x="630" y="2039">5</text><text x="749" y="2163">6</text><text x="711" y="2165">7</text><text x="634" y="2103">8</text>
    <text x="615" y="2073">9</text><text x="772" y="2129">10</text><text x="708" y="2125">11</text><text x="679" y="2107">12</text>
    <text x="666" y="2205">13</text><text x="668" y="2154">14</text><text x="613" y="2180">15</text><text x="710" y="2216">16</text>
    <text x="653" y="2250">17</text><text x="721" y="2199">18</text>
  </g>
</svg>
<ul class="abs country-list" style="left:98px;top:2205px">
  <li class="active">1. USA</li><li>2. Canada</li><li>3. UK</li><li>4. France</li><li>5. Bosnia</li><li>6. UAE</li><li>7. Qatar</li><li>8. Libya</li><li>9. Tunisia</li>
</ul>
<ul class="abs country-list" style="left:192px;top:2205px">
  <li>10.Afghanistan</li><li>11. Iraq</li><li>12. Turkey</li><li>13. Sudan</li><li>14. Egypt</li><li>15. Central African Republic</li><li>16. Somalia</li><li>17. Rwanda</li><li>18. Somaliland</li>
</ul>

<!-- Footer -->
<footer class="abs site-footer"></footer>
<div class="abs footer-col" style="left:82px">
  <svg width="16" height="16" viewBox="0 0 16 16"><path d="M4 1 L6.5 5 L5 6.5 C6 9 7 10 9.5 11 L11 9.5 L15 12 L13 15 C7 15 1 9 1 3 Z" fill="#6d6d6d"/></svg>
  <p style="margin-top:14px">t: +44 (0)131 555 0142<br>f: +44 (0)131 555 0187</p>
</div>
<div class="abs footer-divider" style="left:417px"></div>
<div class="abs footer-col" style="left:426px">
  <svg width="18" height="14" viewBox="0 0 18 14"><rect x="1" y="1" width="16" height="12" fill="none" stroke="#6d6d6d" stroke-width="1.5"/><path d="M1 1 L9 8 L17 1" fill="none" stroke="#6d6d6d" stroke-width="1.5"/></svg>
  <p style="margin-top:16px">e: enquiries@morvanegs.example</p>
</div>
<div class="abs footer-divider" style="left:766px"></div>
<div class="abs footer-col" style="left:770px">
  <svg width="14" height="18" viewBox="0 0 14 18"><path d="M7 17 C3 11 1 8 1 6 A6 6 0 0 1 13 6 C13 8 11 11 7 17 Z" fill="none" stroke="#6d6d6d" stroke-width="1.5"/><circle cx="7" cy="6" r="2" fill="#6d6d6d"/></svg>
  <p style="margin-top:12px">Lorem ipsum, Level 12, Calder House<br>4 Harlow Square, Edinburgh EH2 4AB</p>
</div>
<span class="abs social" style="left:514px"></span>
<span class="abs social is-active" style="left:548px"></span>
<span class="abs social" style="left:582px"></span>
<span class="abs social" style="left:616px"></span>
<span class="abs social" style="left:650px"></span>
<p class="abs copyright">© 2015. YOURSITE. ALL RIGHTS RESERVED</p>

</body>
</html>
```